Interior Design/ New Construction interior finishes

Interior Design Website

Target Market(s)

Home builders, New Construction, Renovations, Public

Industry/Entity Type

Construction

Coding

Coded - Design and coding required

Number of Pages Required

1 page

Font styles to use
Sans Serif

Colors

Designer to choose colors to be used in the design.

Requirements
Must have
• Section to upload pictures of projects
• Simple and modern design
• Designer 1 details about myself
• Logo
• Upload section for photos for future jobs
Nice to have
• Sections they can click on to see certain rooms in a house
• Decorating, floral arrangements, holiday decorating.
• I have lots of before and after as well. Maybe a section for those.

```html
<!DOCTYPE html>
<html lang="en">
<head>
<meta charset="utf-8">
<meta name="format-detection" content="telephone=no">
<title>Tellman Designs – Interior Design &amp; New Construction</title>
<link href="https://fonts.googleapis.com/css2?family=Open+Sans:wght@300;400;600;700;800&display=swap" rel="stylesheet">
<style>
:root{
  --ink:#111111;
  --text:#444444;
  --muted:#777777;
  --white:#ffffff;
  --light:#f0f0f0;
  --line:#cccccc;
  --dark-panel:#33363a;
  --footer:#000000;
  --social:#1c75bc;
}
*{margin:0;padding:0;box-sizing:border-box}
html,body{width:1200px;height:3805px;overflow:hidden;background:var(--white);font-family:"Open Sans",Arial,sans-serif;color:var(--text)}
.page{position:relative;width:1200px;height:3805px}
section,header,footer{position:absolute;left:0;width:1200px}
.abs{position:absolute}
.btn{display:inline-block;background:var(--ink);color:var(--white);font-size:11px;font-weight:700;letter-spacing:.5px;padding:7px 12px}
.btn-outline{display:inline-block;border:2px solid var(--ink);color:var(--ink);font-size:12px;font-weight:700;padding:7px 14px}
.rule{width:58px;height:5px;background:#999}

/* header */
.site-header{top:0;height:110px;background:var(--white)}
.brand{left:132px;top:24px;display:flex;align-items:center;gap:12px}
.brand-mark{width:52px;height:52px;border:3px solid var(--ink);border-radius:50%}
.brand-name{font-size:22px;font-weight:400;color:var(--ink);letter-spacing:1.5px}
.call{left:772px;top:18px;display:flex;align-items:center;gap:12px}
.call small{display:block;font-size:10px;font-weight:600;color:var(--ink)}
.call strong{display:block;font-size:18px;font-weight:400;color:var(--ink);line-height:1.1}
.search{left:952px;top:22px;width:116px;height:32px;border:1px solid var(--line);font-size:9px;padding:9px 10px;color:var(--ink)}
.search svg{position:absolute;right:8px;top:9px}
.nav{left:582px;top:72px;display:flex;gap:6px}
.nav a{font-size:12px;font-weight:600;color:var(--ink);padding:5px 8px;text-decoration:none}
.nav a.active{background:#333;color:var(--white)}

/* hero */
.hero{top:110px;height:550px;background:linear-gradient(180deg,#c8d4dc 0%,#a48a70 45%,#7a6250 70%,#5f7c5a 100%)}
.hero-copy{left:723px;top:60px}
.hero-copy h1{font-size:27px;font-weight:800;color:var(--ink)}
.hero-copy p{font-size:17px;color:#555;margin:6px 0 14px}
.dots{left:570px;top:498px;display:flex;gap:16px}
.dots span{width:9px;height:9px;border-radius:50%;background:var(--white)}
.dots span.on{width:14px;height:14px;margin-top:-2px;border:2px solid var(--white);background:transparent}

/* services */
.services{top:660px;height:532px}
.services-head{left:132px;top:92px}
.services-head .rule{background:#999;margin-bottom:22px}
.services-head h2{font-size:30px;font-weight:300;color:var(--ink);line-height:1.1}
.services-head h2 b{font-weight:800}
.services-line{left:278px;top:225px;width:3px;height:200px;background:var(--line)}
.view-all{left:132px;top:372px;width:150px;height:48px;background:#dcdcdc;font-size:11px;font-weight:700;color:#555;text-align:center;line-height:48px}
.service{top:86px;width:221px}
.service .photo{height:195px}
.service h3{font-size:14px;font-weight:400;color:var(--ink);margin-top:30px}
.service h3 b{font-weight:800}
.service p{font-size:11px;line-height:1.45;margin:10px 0 14px;color:var(--text)}

/* welcome */
.welcome{top:1192px;height:543px}
.welcome-photo{left:0;top:0;width:617px;height:543px;background:linear-gradient(135deg,#6d6a5c 0%,#9b7b5c 50%,#cfa679 100%)}
.welcome-box{left:254px;top:117px;width:423px;height:317px;border:4px solid var(--white);background:rgba(50,50,50,.85);padding:40px 44px;color:var(--white)}
.welcome-box h4{font-size:16px;font-weight:700}
.welcome-box h2{font-size:33px;font-weight:800;line-height:1.1;margin:4px 0 14px;white-space:nowrap}
.welcome-box p{font-size:12px;line-height:1.5;margin-bottom:22px}
.welcome-box .btn{border:1px solid var(--white)}
.welcome-panel{left:617px;top:0;width:583px;height:543px;background:var(--dark-panel)}
.feature{left:140px;width:420px;height:124px;display:flex;align-items:center;gap:30px;color:var(--white)}
.feature h3{font-size:13px;font-weight:800}
.feature p{font-size:11px;line-height:1.4;margin-top:6px;color:#ddd}
.feature .thumb{width:96px;height:96px;border-radius:50%;border:3px solid #ddd;flex:none}
.divider{left:120px;width:440px;height:1px;background:#555}

/* testimonials */
.testimonials{top:1735px;height:493px;text-align:center}
.testimonials .rule{position:absolute;left:571px;top:69px}
.testimonials h2{position:absolute;top:88px;width:100%;font-size:22px;font-weight:800;color:var(--ink)}
.quote{left:366px;top:182px;width:468px;font-size:12px;line-height:1.65;color:var(--text)}
.quote-mark{font-size:80px;color:#ddd;font-weight:800;line-height:1}
.avatar{left:572px;top:300px;width:56px;height:56px;border-radius:50%;background:linear-gradient(#cfd6dc,#6a7784)}
.person{left:500px;top:372px;width:200px;font-size:12px}
.person b{color:var(--ink);font-weight:800;display:block}
.arrow-btn{top:378px;width:40px;height:28px;background:#e6e6e6;display:flex;align-items:center;justify-content:center}

/* showcase */
.showcase{top:2228px;height:697px;background:var(--light)}
.showcase-photo{left:190px;top:65px;width:495px;height:386px;background:linear-gradient(160deg,#9fb0c6 0%,#d9d0c3 45%,#8f6f55 100%)}
.counter{left:632px;top:430px;font-size:12px;color:var(--ink)}
.showcase-copy{left:738px;top:120px;width:300px}
.showcase-copy h2{font-size:30px;font-weight:300;color:var(--ink);line-height:1.15}
.showcase-copy h2 b{font-weight:800}
.showcase-copy p{font-size:13px;line-height:1.55;margin:18px 0 26px}
.thumbs{left:190px;top:509px;display:flex;gap:16px}
.thumbs div{width:148px;height:110px}

/* before after */
.before-after{top:2925px;height:513px;text-align:center}
.before-after .rule{position:absolute;left:571px;top:57px}
.before-after h2{position:absolute;top:85px;width:100%;font-size:22px;font-weight:800;color:var(--ink)}
.ba-item{top:163px;width:292px;text-align:left}
.ba-item .photo{height:266px}
.ba-item h3{font-size:12px;font-weight:800;color:var(--ink);margin-top:12px}
.round-arrow{top:280px;width:46px;height:46px;border-radius:50%;background:var(--white);box-shadow:0 1px 4px rgba(0,0,0,.3);display:flex;align-items:center;justify-content:center}

/* footer */
.site-footer{top:3438px;height:367px;background:var(--footer);color:var(--white)}
.footer-brand{left:136px;top:100px;display:flex;align-items:center;gap:14px}
.footer-brand .brand-mark{border-color:var(--white);width:70px;height:70px}
.footer-brand span{font-size:24px;letter-spacing:2px}
.fcol{top:62px}
.fcol h4{font-size:12px;font-weight:800;margin-bottom:18px}
.fcol li{list-style:none;font-size:11px;line-height:1.6;display:flex;gap:12px;align-items:flex-start;margin-bottom:10px}
.fcol.menu li{margin:0}
.social-dot{width:24px;height:24px;border-radius:50%;background:var(--social);flex:none}
.social li{align-items:center;margin-bottom:14px}
.footer-rule{left:132px;top:271px;width:936px;height:1px;background:#333}
.copyright{top:314px;width:100%;text-align:center;font-size:11px}
</style>
</head>
<body>
<div class="page">

<header class="site-header">
  <div class="abs brand"><span class="brand-mark"></span><span class="brand-name">Tellman Designs</span></div>
  <div class="abs call">
    <svg width="26" height="26" viewBox="0 0 26 26"><circle cx="13" cy="13" r="12" fill="none" stroke="#111" stroke-width="1.5"/><path d="M9 8c0 5 4 9 9 9l1-2-3-1-1 1c-2-1-3-2-4-4l1-1-1-3z" fill="#111"/></svg>
    <div><small>CALL US NOW</small><strong>555.014.2290</strong></div>
  </div>
  <div class="abs search">SEARCH<svg width="12" height="12" viewBox="0 0 12 12"><circle cx="5" cy="5" r="3.5" fill="none" stroke="#111" stroke-width="1.6"/><path d="M8 8l3 3" stroke="#111" stroke-width="1.6"/></svg></div>
  <nav class="abs nav"><a class="active">HOME</a><a>INTERIOR</a><a>CONSTRUCTION</a><a>SERVICES</a><a>PROJECTS</a><a>CONTACT US</a></nav>
</header>

<section class="hero" role="img" aria-label="Photo of a newly built brick house with arched patio and pool">
  <div class="abs hero-copy"><h1>NEW CONSTRUCTION</h1><p>Lorem Ipsum is simply dummy text of the printing</p><span class="btn-outline">READ MORE</span></div>
  <div class="abs dots"><span></span><span></span><span class="on"></span><span></span><span></span></div>
</section>

<section class="services">
  <div class="abs services-head"><div class="rule"></div><h2>OUR<br><b>SERVICES</b></h2></div>
  <div class="abs services-line"></div>
  <div class="abs view-all">VIEW ALL SERVICES</div>
  <article class="abs service" style="left:355px"><div class="photo" role="img" aria-label="Bedroom interior photo" style="background:linear-gradient(160deg,#b9a58c,#6d5646)"></div><h3>INTERIOR <b>DESIGNING</b></h3><p>Lorem Ipsum is simply dummy text of the printing and types etting industry</p><span class="btn">READ MORE</span></article>
  <article class="abs service" style="left:601px"><div class="photo" role="img" aria-label="New house exterior photo" style="background:linear-gradient(180deg,#c7d6e2,#947c66 60%,#5c7250)"></div><h3>NEW <b>CONSTRUCTION</b></h3><p>Lorem Ipsum is simply dummy text of the printing and types etting industry</p><span class="btn">READ MORE</span></article>
  <article class="abs service" style="left:845px"><div class="photo" role="img" aria-label="White kitchen photo" style="background:linear-gradient(180deg,#e8e8e6,#bdbab4)"></div><h3>DESIGN &amp; <b>BUILD</b></h3><p>Lorem Ipsum is simply dummy text of the printing and types etting industry</p><span class="btn">READ MORE</span></article>
</section>

<section class="welcome">
  <div class="abs welcome-photo" role="img" aria-label="Living room interior with wicker furniture"></div>
  <div class="abs welcome-box"><h4>WELCOME TO</h4><h2>TELLMAN DESIGNS</h2><p>Lorem Ipsum is simply dummy text of the printing and types etting industry it look like readable English. Many desktop publishing packages and web page editors now use Lorem Ipsum as their default model.</p><span class="btn">READ MORE</span></div>
  <div class="abs welcome-panel">
    <div class="abs feature" style="top:52px"><div class="thumb" role="img" aria-label="Decorated table setting" style="background:linear-gradient(#eee,#9a9a9a)"></div><div><h3>DECORATING</h3><p>Lorem Ipsum is simply dummy text<br>of the printing and types etting<br>industry it look like</p></div></div>
    <div class="abs divider" style="top:191px"></div>
    <div class="abs feature" style="top:206px"><div class="thumb" role="img" aria-label="Floral arrangement" style="background:radial-gradient(#e05a8a,#6f8f4a)"></div><div><h3>FLORAL ARRANGEMENTS</h3><p>Lorem Ipsum is simply dummy text<br>of the printing and types etting<br>industry it look like</p></div></div>
    <div class="abs divider" style="top:345px"></div>
    <div class="abs feature" style="top:360px"><div class="thumb" role="img" aria-label="Decorated holiday tree" style="background:radial-gradient(#3f6b3a,#c9c2b5)"></div><div><h3>HOLIDAY DECORATING</h3><p>Lorem Ipsum is simply dummy text<br>of the printing and types etting<br>industry it look like</p></div></div>
  </div>
</section>

<section class="testimonials">
  <div class="rule"></div>
  <h2>TESTIMONIALS</h2>
  <div class="abs quote-mark" style="left:322px;top:140px">“</div>
  <p class="abs quote">Lorem Ipsum is simply dummy text of the printing and types etting industry it look like readable English. Many desktop publishing packages and web page editors now use Lorem Ipsum as their default model for 'lorem ipsum' will uncover many web sites still in their infancy. Various versions have evolved over.</p>
  <div class="abs quote-mark" style="left:790px;top:272px">”</div>
  <div class="abs avatar" role="img" aria-label="Client portrait"></div>
  <div class="abs person"><b>MARTIN DELACROIX</b>England</div>
  <div class="abs arrow-btn" style="left:468px"><svg width="18" height="10"><path d="M17 5H2M6 1L2 5l4 4" fill="none" stroke="#666" stroke-width="1.4"/></svg></div>
  <div class="abs arrow-btn" style="left:692px"><svg width="18" height="10"><path d="M1 5h15M12 1l4 4-4 4" fill="none" stroke="#666" stroke-width="1.4"/></svg></div>
</section>

<section class="showcase">
  <div class="abs showcase-photo" role="img" aria-label="Children's room with staircase loft bed"></div>
  <div class="abs counter">1 of 10</div>
  <div class="abs showcase-copy"><h2>OUR WORK<br><b>SHOWCASE</b></h2><p>Lorem Ipsum is simply dummy text of the printing and types etting industry it look like readable English. Many desktop publishing packages and web page editors now use Lorem Ipsum as their default model.</p><span class="btn">READ MORE</span></div>
  <svg class="abs" style="left:128px;top:554px" width="24" height="16"><path d="M23 8H3M9 2L3 8l6 6" fill="none" stroke="#111" stroke-width="2"/></svg>
  <div class="abs thumbs">
    <div role="img" aria-label="Project photo: living room fireplace" style="background:linear-gradient(#8a7c6e,#4d423a)"></div>
    <div role="img" aria-label="Project photo: kitchen" style="background:linear-gradient(#6e7076,#2f3236)"></div>
    <div role="img" aria-label="Project photo: empty room" style="background:linear-gradient(#c9c5c0,#6f6b66)"></div>
    <div role="img" aria-label="Project photo: bathroom" style="background:linear-gradient(#e6e6e6,#9e9e9e)"></div>
    <div role="img" aria-label="Project photo: white interior" style="background:linear-gradient(#f0f0f0,#b0b0b0)"></div>
  </div>
  <svg class="abs" style="left:1042px;top:554px" width="24" height="16"><path d="M1 8h20M15 2l6 6-6 6" fill="none" stroke="#111" stroke-width="2"/></svg>
</section>

<section class="before-after">
  <div class="rule"></div>
  <h2>BEFORE &amp; AFTER</h2>
  <article class="abs ba-item" style="left:132px"><div class="photo" role="img" aria-label="Before and after of a room renovation" style="background:linear-gradient(90deg,#a89b8a,#d8d6d2 50%,#8f9aa0)"></div><h3>HEADING 1</h3></article>
  <article class="abs ba-item" style="left:452px"><div class="photo" role="img" aria-label="Before and after of a building facade" style="background:linear-gradient(160deg,#4f7fbf,#c9b48d 55%,#2f3f52)"></div><h3>HEADING 2</h3></article>
  <article class="abs ba-item" style="left:774px"><div class="photo" role="img" aria-label="Before and after of an apartment interior" style="background:linear-gradient(90deg,#e0ddd8,#a08060)"></div><h3>HEADING 3</h3></article>
  <div class="abs round-arrow" style="left:109px"><svg width="18" height="14"><path d="M17 7H2M7 1L1 7l6 6" fill="none" stroke="#111" stroke-width="2"/></svg></div>
  <div class="abs round-arrow" style="left:1043px"><svg width="18" height="14"><path d="M1 7h15M11 1l6 6-6 6" fill="none" stroke="#111" stroke-width="2"/></svg></div>
</section>

<footer class="site-footer">
  <div class="abs footer-brand"><span class="brand-mark"></span><span>Tellman Designs</span></div>
  <div class="abs fcol" style="left:474px">
    <h4>CONTACT US</h4>
    <ul>
      <li><svg width="10" height="14"><path d="M5 0a5 5 0 015 5c0 4-5 9-5 9S0 9 0 5a5 5 0 015-5z" fill="#fff"/><circle cx="5" cy="5" r="2" fill="#000"/></svg><span>48 Meadow Lane<br>Brookfield, IL 60000</span></li>
      <li><svg width="12" height="12"><path d="M2 1c0 5 4 10 9 10l1-2-3-1-1 1c-2-1-3-2-4-4l1-1-1-3z" fill="#fff"/></svg><span>555.014.2290</span></li>
      <li><svg width="12" height="10"><rect width="12" height="10" fill="#fff"/><path d="M0 0l6 5 6-5" fill="none" stroke="#000"/></svg><span>info@tellmandesigns.com</span></li>
    </ul>
  </div>
  <div class="abs fcol menu" style="left:731px">
    <h4>MENU</h4>
    <ul><li>Home</li><li>Interior</li><li>Construction</li><li>Services</li><li>Projects</li><li>Contact Us</li></ul>
  </div>
  <div class="abs fcol social" style="left:936px">
    <h4>CONNECT WITH US</h4>
    <ul><li><span class="social-dot"></span>Friendspace</li><li><span class="social-dot"></span>Chirper</li><li><span class="social-dot"></span>WorkLink</li></ul>
  </div>
  <div class="abs footer-rule"></div>
  <p class="abs copyright">Copyrights @ 2018 All Rights Reserved</p>
</footer>

</div>
</body>
</html>
```